Financial Services Consultant needs a business card

We need a business card for a new consulting company based in Melbourne called
"Quelbrook Insights". Tagline is Measure, Monitor, Save
We would like to see business card designs that are in line with the minimal style of the website www.quelbrook-insights.example
The font I have used on the website is Proxima Nova and would like the same or similar font used on the business card with a minimal design in line with the website Two sided with "QUELBROOK INSIGHTS" MEASURE, MONITOR, SAVE on one side and name, title and contact details on the otther
Updates

Hi All, thanks for your submissions, much appreciated.

I have recently added some colour to my webiste, it is hex #3a7b74 for those that wish to use it
Thanks

Hi all

thanks very much for your design submissions I am very impressed and they are much appreciated.

Interms of general feedback please find below;

Colour: I am trying to stick to a minimal design and colour scheme for my website which is still under construction, up to 3 colours( www.quelbrook-insights.example) it is currently black and white with a small amount of blue/green but I am open to suggestion/interpretations for a consulting company.

Card: I dont mind if it has rounded edges or straight, I was thinking about using a letterpress card if possible

Detail: the detail on the card will include; Name, Title, Mobile, Personal Email, Business Email,Web,Business Address

Once again thanks for submissions

Industry/Entity Type

Business

```html
<!DOCTYPE html>
<html lang="en">
<head>
<meta charset="utf-8">
<title>Quelbrook Insights — Business Card</title>
<link rel="stylesheet" href="https://fonts.googleapis.com/css2?family=Montserrat:wght@400;500;600;700&family=Open+Sans:wght@400;600&display=swap">
<style>
  :root {
    --page-bg: #ecebe8;
    --card-bg: #ffffff;
    --ink: #151515;
    --ink-soft: #3a3a3a;
    --teal: #3a7b74;
    --rule: #9a9a9a;
    --shadow: rgba(0, 0, 0, 0.14);
  }
  * { box-sizing: border-box; margin: 0; padding: 0; }
  html, body {
    width: 1200px;
    height: 720px;
    overflow: hidden;
  }
  body {
    background: var(--page-bg);
    display: flex;
    align-items: center;
    justify-content: center;
    gap: 44px;
    font-family: "Open Sans", Arial, sans-serif;
    color: var(--ink);
  }
  .card {
    position: relative;
    width: 540px;
    height: 309px;
    background: var(--card-bg);
    box-shadow: 0 6px 18px var(--shadow);
    overflow: hidden;
  }
  .wordmark {
    font-family: "Montserrat", Arial, sans-serif;
    font-weight: 700;
    letter-spacing: 0.13em;
    color: var(--ink);
    white-space: nowrap;
  }

  /* Contact side */
  .card-front .brand {
    position: absolute;
    top: 38px;
    left: 0;
    right: 0;
    text-align: center;
  }
  .card-front .wordmark { font-size: 25px; }
  .tagline {
    margin-top: 8px;
    font-size: 14px;
    color: var(--ink-soft);
    letter-spacing: 0.02em;
  }
  .person {
    position: absolute;
    top: 128px;
    left: 0;
    right: 0;
    text-align: center;
    font-size: 15px;
  }
  .person .name { font-weight: 600; color: var(--ink); }
  .person .title { font-size: 12px; color: var(--teal); }
  .contact {
    position: absolute;
    top: 172px;
    left: 0;
    right: 0;
    display: flex;
    justify-content: center;
    font-size: 12px;
    color: var(--ink-soft);
    line-height: 1.65;
  }
  .contact .address {
    text-align: right;
    padding: 22px 12px 0 0;
    border-right: 1px solid var(--rule);
  }
  .contact .lines { padding-left: 10px; }
  .contact .line { display: flex; align-items: center; gap: 6px; }
  .contact svg { width: 11px; height: 11px; }
  .card-bands {
    position: absolute;
    left: 0;
    bottom: 0;
    width: 540px;
    height: 309px;
  }

  /* Brand side */
  .card-back {
    display: flex;
    flex-direction: column;
    align-items: center;
    justify-content: center;
  }
  .card-back .wordmark { font-size: 28px; }
  .card-back .web {
    margin-top: 14px;
    font-size: 15px;
    letter-spacing: 0.2em;
    color: var(--ink-soft);
  }
</style>
</head>
<body>

  <section class="card card-front" aria-label="Business card, contact side">
    <div class="brand">
      <div class="wordmark">QUELBROOK INSIGHTS</div>
      <p class="tagline">Measure, Monitor, Save</p>
    </div>

    <p class="person"><span class="name">Your Name,</span> <span class="title">Title</span></p>

    <div class="contact">
      <div class="address">
        Street Name, City Name<br>State Zip Code
      </div>
      <div class="lines">
        <div class="line">
          <svg viewBox="0 0 12 12" aria-hidden="true"><circle cx="6" cy="6" r="5.3" fill="none" stroke="currentColor" stroke-width="1"/><path d="M4 3.3l1 1.6-.6.6c.4.9 1 1.5 1.9 1.9l.6-.6 1.6 1-.5 1c-2.4-.2-4.4-2.2-4.6-4.6z" fill="currentColor"/></svg>
          <span>123-555-0189</span>
        </div>
        <div class="line">
          <svg viewBox="0 0 12 12" aria-hidden="true"><circle cx="6" cy="6" r="5.3" fill="none" stroke="currentColor" stroke-width="1"/><ellipse cx="6" cy="6" rx="2.2" ry="5.3" fill="none" stroke="currentColor" stroke-width="0.8"/><path d="M0.8 6h10.4M1.8 3.3h8.4M1.8 8.7h8.4" stroke="currentColor" stroke-width="0.8"/></svg>
          <span>www.quelbrook-insights.example</span>
        </div>
      </div>
    </div>

    <svg class="card-bands" viewBox="0 0 540 309" aria-hidden="true">
      <polygon points="0,293 252,293 242,309 0,309" fill="var(--ink)"/>
      <polygon points="254,286 270,266 540,258 540,274" fill="var(--teal)"/>
    </svg>
  </section>

  <section class="card card-back" aria-label="Business card, brand side">
    <div class="wordmark">QUELBROOK INSIGHTS</div>
    <p class="web">www.quelbrook-insights.example</p>
  </section>

</body>
</html>
```